VELMOR Website Design

We need a website designed for our company VELMOR. We are a luxury lifestyle club that will provide benefits and services for our members. The site should be clean & sleek, preferably using black and white (or darker colors). (example sites: stravenhall.example, plinth.example)

Here is a link of a sample page I did using wix. (https://dunmere7.sitehostly.example/mysite) This can be used to get a general idea.

Target Market(s)

Upper Middle Class in the United States

Number of Pages Required

5+ page

Font styles to use
Sans Serif
Other font styles liked:
• Arial (or other similar fonts)

Requirements
Must have
• A clean design that is eye-catching and speaks to our company.
Nice to have
• Ideas for copy.

```html
<!DOCTYPE html>
<html lang="en">
<head>
<meta charset="utf-8">
<title>VELMOR – Indication of Interest</title>
<link rel="stylesheet" href="https://fonts.googleapis.com/css2?family=Figtree:wght@400;500&display=swap">
<style>
  :root {
    --header-bg: #141414;
    --footer-bg: #000000;
    --hero-dark: #22232b;
    --hero-mid: #2f303b;
    --hero-light: #4a4c5c;
    --panel-bg: rgba(4, 4, 6, 0.93);
    --text: #ffffff;
    --muted: #8a8a8e;
    --field-border: #9a9aa0;
    --button-bg: #ffffff;
    --button-text: #111111;
  }
  * { box-sizing: border-box; margin: 0; padding: 0; }
  html, body { width: 1200px; height: 818px; overflow: hidden; background: var(--footer-bg); }
  body { position: relative; font-family: "Figtree", Arial, sans-serif; color: var(--text); }

  .site-header {
    position: absolute; left: 0; top: 0; width: 1200px; height: 64px;
    background: var(--header-bg);
  }
  .brand {
    position: absolute; left: 236px; top: 13px;
    font-size: 27px; font-weight: 400; letter-spacing: 0.5px; line-height: 36px;
  }
  .main-nav { position: absolute; top: 22px; left: 0; width: 1200px; }
  .main-nav a {
    position: absolute; color: var(--text); text-decoration: none;
    font-size: 12.5px; line-height: 16px; white-space: nowrap;
  }

  .hero {
    position: absolute; left: 0; top: 64px; width: 1200px; height: 618px;
    background: linear-gradient(160deg, var(--hero-mid) 0%, var(--hero-dark) 45%, var(--hero-mid) 75%, var(--hero-light) 100%);
  }

  .interest-panel {
    position: absolute; left: 190px; top: 110px; width: 822px; height: 500px;
    background: var(--panel-bg); text-align: center;
  }
  .intro {
    position: absolute; left: 120px; top: 57px; width: 582px;
    font-size: 12.5px; line-height: 15px;
  }
  .panel-title {
    position: absolute; left: 0; top: 144px; width: 822px;
    font-size: 27px; font-weight: 400; line-height: 34px; letter-spacing: 0.2px;
  }
  .field {
    position: absolute; left: 242px; width: 336px; height: 41px;
    border: 1px solid var(--field-border); border-radius: 21px;
    background: transparent; color: var(--text);
    font-family: inherit; font-size: 12.5px; padding-left: 25px; outline: none;
  }
  .field::placeholder { color: var(--muted); }
  .submit {
    position: absolute; left: 334px; top: 431px; width: 151px; height: 23px;
    background: var(--button-bg); color: var(--button-text); border: none;
    border-radius: 12px; font-family: inherit; font-size: 12px;
  }

  .site-footer {
    position: absolute; left: 0; top: 682px; width: 1200px; height: 136px;
    background: var(--footer-bg); text-align: center;
  }
  .social-list { position: absolute; left: 504px; top: 50px; display: flex; gap: 6px; }
  .social-list span {
    display: block; width: 22px; height: 22px; background: var(--text); border-radius: 2px;
  }
  .copyright {
    position: absolute; left: 0; top: 100px; width: 1200px;
    font-size: 12.5px; line-height: 16px;
  }
</style>
</head>
<body>
  <header class="site-header">
    <div class="brand">VELMOR</div>
    <nav class="main-nav">
      <a href="#" style="left:502px">HOME</a>
      <a href="#" style="left:570px">ABOUT</a>
      <a href="#" style="left:644px">SERVICES AND BENEFITS</a>
      <a href="#" style="left:820px">APPLY</a>
      <a href="#" style="left:888px">CONTACT US</a>
    </nav>
  </header>

  <section class="hero" role="img" aria-label="Photo of a desk from above with a cup of coffee, coffee beans, a laptop and a notebook"></section>

  <form class="interest-panel">
    <p class="intro">Hey - Thanks for your interest! We will begin accepting applications in 2019. In the meantime, simply fill out the indication of interest below and we will be in touch once we begin accepting applications!</p>
    <h1 class="panel-title">INDICATION OF INTEREST</h1>
    <input class="field" style="top:236px" type="text" placeholder="Fullname">
    <input class="field" style="top:294px" type="email" placeholder="Email">
    <input class="field" style="top:352px" type="tel" placeholder="Phone Number">
    <button class="submit" type="button">Submit</button>
  </form>

  <footer class="site-footer">
    <div class="social-list" aria-label="Social links">
      <span></span><span></span><span></span><span></span><span></span><span></span><span></span>
    </div>
    <p class="copyright">© 2018 VELMOR</p>
  </footer>
</body>
</html>
```